Kelvor Guard Installations - Alarm and CCTV installation Flyer

Need a flyer designed that grabs the attention of potential customers, we need the price to stand out the most to grab people’s attention, whether they are residential or commercial.We are a security company based in Brentwood Essex but cover London and the home counties. here is our website to take a look at www.kelvorguardinstalls.co.uk. We want them to know we install complete alarm and Cctv systems and will keep them “safe”

Target Market(s)

residential and commercial property

Colors
f37122

Requirements
Must have
• on one side
• large clear logo - professional design
• - Intruder Alarms starting from £495 + VAT. (Big text)
• - £150 discount on installations
• *terms and conditions apply (small text)
• - Not happy with your current provider? Free of charge no obligation take over survey and quotation and up to £100 off
• - CCTV systems starting from £595 + VAT (based on 2 cameras)
• Kelvor Guard Installations are always there, always available, wherever and whenever you need us.
• Large telephone number at the bottom 01632 908417
• Address / email / website as a footer * see website for details
• on second side
• large and bold
• Are you looking to keep you and your premises safe?
• - Kelvor Guard Installations install, maintain and repair all intruder alarms, CCTV, intercom and access control
• - View, control and manage your security systems anywhere in the world
• - Feel at ease with monitoring services & police response tailored to suit you and your business
• - Kelvor Guard can takeover any existing security system and offer maintenance checks to guarantee the best performance for you and your premises
• - Kelvor Guard understand that being security conscious is ever increasing, protecting your property and family is a number one priority
• - Our fully insured and accredited team offer quality, safety and cost efficiency throughout the whole process
• - Kelvor Guard Installations are using the latest cloud-based technology to stay connected with your home and business 24/7
• If you are looking to improve the security in your home, office or commercial property then call a member of our team today for a free quote.
• Fully insured and accredited
• Tradevouch logo and NQPRB Intruder and CCTV logos
• Logo somewhere on page and
• Telephone number
• Address / email / website as footer
Nice to have
• We would like to have the text saying
• Intruder alarms installed from £495 + vat the biggest text on the page. Most likely the £495 part the largest.
• Also would like “not happy with your current provider” more obvious
• We would like use our company colours - Orange/White/black

```html
<!DOCTYPE html>
<html lang="en">
<head>
<meta charset="utf-8">
<title>Kelvor Guard Installations – Alarm &amp; CCTV Flyer</title>
<link href="https://fonts.googleapis.com/css2?family=Oswald:wght@400;500;600;700&family=Lato:ital,wght@0,400;0,700;0,900;1,700&display=swap" rel="stylesheet">
<style>
:root{
  --orange:#f37122;
  --orange-deep:#e0611a;
  --ink:#262626;
  --charcoal:#303030;
  --light-band:#ececec;
  --white:#ffffff;
  --backdrop:#a4a4a4;
}
*{margin:0;padding:0;box-sizing:border-box}
html,body{width:1200px;height:902px;overflow:hidden;background:var(--backdrop)}
body{position:relative;font-family:'Lato',Arial,sans-serif;color:var(--ink)}
.flyer{position:absolute;overflow:hidden;background:var(--white)}
.abs{position:absolute;white-space:nowrap}
.cond{font-family:'Oswald','Arial Narrow',sans-serif}

/* ---------- FRONT ---------- */
.flyer-front{left:87px;top:95px;width:478px;height:670px}
.front-shapes{position:absolute;inset:0}
.camera-photo{left:223px;top:58px;width:255px;height:235px;border-radius:48% 0 0 48%;
  background:radial-gradient(circle at 42% 52%,#3a3a3a 0 16%,#8a8a8a 30%,#d6d6d6 55%,#f1f1f1 78%,rgba(255,255,255,0) 100%)}
.brand-mark{left:94px;top:18px;width:50px;height:50px;border-radius:50%;background:var(--orange)}
.brand-name{left:20px;top:80px;width:198px;text-align:center;color:var(--orange);font-weight:700;font-size:24px;line-height:1}
.brand-sub{left:20px;top:108px;width:198px;text-align:center;color:var(--orange);font-weight:700;font-size:13px;letter-spacing:2px;line-height:1}
.brand-rule{height:2px;width:22px;background:var(--orange)}
.alarm-title{left:39px;top:183px;color:var(--white);font-weight:900;font-size:36px;line-height:1.02}
.alarm-from{left:39px;top:266px;color:var(--white);font-weight:700;font-size:20px}
.alarm-price{left:39px;top:285px;color:var(--ink);font-weight:600;font-size:41px;line-height:1.1}
.discount-badge{left:53px;top:351px;width:155px;height:141px}
.discount-text{left:53px;top:368px;width:155px;text-align:center}
.discount-amount{color:var(--orange);font-weight:600;font-size:40px;line-height:1}
.discount-word{font-weight:700;font-size:19px;line-height:1.05;color:var(--ink)}
.discount-on{color:var(--orange);font-weight:700;font-size:10px}
.discount-terms{font-style:italic;font-size:7.5px;line-height:1.15;margin-top:2px}
.provider-question{left:252px;top:344px;color:var(--white);font-weight:500;font-size:24px;line-height:1.15;text-transform:uppercase}
.offer-box{left:252px;top:414px;width:196px;height:45px;background:var(--white);border-radius:3px;box-shadow:0 1px 3px rgba(0,0,0,.4)}
.offer-free{left:8px;top:3px;color:var(--orange);font-weight:500;font-size:13px;line-height:1.3}
.offer-small{left:8px;top:22px;font-weight:500;font-size:6.5px;line-height:1.4;color:var(--ink)}
.offer-amount{left:100px;top:-4px;font-weight:600;font-size:36px;color:var(--ink);line-height:1.4}
.offer-off{left:163px;top:15px;width:36px;text-align:center;color:var(--orange);font-weight:700;font-size:14px;line-height:1;transform:rotate(-90deg)}
.cctv-line{left:29px;top:507px;color:var(--white);font-weight:700;font-size:15px}
.cctv-note{left:55px;top:527px;color:var(--white);font-weight:700;font-size:11px;letter-spacing:.5px}
.cctv-price-disc{left:280px;top:472px;width:102px;height:84px;border-radius:50%;
  background:radial-gradient(circle at 50% 35%,#ff9a50,var(--orange) 55%,var(--orange-deep));
  border:4px solid #d9d9d9;box-shadow:0 0 0 2px #555;display:flex;align-items:center;justify-content:center;z-index:2}
.cctv-price-disc span{font-weight:600;font-size:36px;color:var(--ink)}
.cctv-vat{left:391px;top:505px;color:var(--white);font-weight:700;font-size:20px}
.call-band{left:0;top:549px;width:478px;height:74px;background:var(--light-band)}
.call-label{left:34px;top:25px;font-weight:900;font-size:22px;color:var(--ink)}
.call-icon{left:147px;top:22px;width:30px;height:30px}
.call-number{left:193px;top:14px;font-weight:900;font-size:38px;color:var(--orange);line-height:1.2}
.front-footer{left:0;top:623px;width:478px;height:47px;background:var(--charcoal)}
.contact-item{display:flex;align-items:center;gap:6px;color:var(--white);font-size:7.5px;line-height:1.3}
.contact-dot{width:17px;height:17px;border-radius:50%;background:var(--orange);flex:none;display:flex;align-items:center;justify-content:center}

/* ---------- BACK ---------- */
.flyer-back{left:637px;top:147px;width:480px;height:670px}
.back-header{left:0;top:0;width:480px;height:103px;background:var(--orange)}
.header-q1{left:32px;top:20px;font-weight:600;font-size:31px;color:var(--ink);line-height:1.2}
.header-q2{left:30px;top:63px;font-weight:500;font-size:21px;color:var(--white);line-height:1.2}
.header-safe{left:294px;top:14px;font-weight:700;font-size:70px;color:var(--white);line-height:1.1}
.keypad-photo{left:0;top:103px;width:480px;height:235px;
  background:linear-gradient(100deg,#d8d8d8 0%,#eeeeee 18%,#b9bcc1 22%,#dfe2e6 40%,#9fb0c8 55%,#e6e8ea 72%,#f4f4f4 100%)}
.back-dark{left:0;top:338px;width:480px;height:192px;background:var(--charcoal)}
.benefit-list{left:27px;top:20px;width:294px;list-style:none;white-space:normal}
.benefit-list li{position:relative;padding-left:19px;color:var(--white);font-size:7.4px;line-height:1.3;margin-bottom:6px}
.benefit-list li b{font-style:italic;font-weight:700}
.benefit-list li .hl{color:var(--orange)}
.benefit-tick{position:absolute;left:0;top:1px;width:11px;height:11px}
.app-photo{left:323px;top:28px;width:122px;height:160px;border-radius:12px;
  background:linear-gradient(160deg,#1c1c1c,#5b6d88 45%,#d8dfe8 60%,#2a2a2a)}
.back-white{left:0;top:530px;width:480px;height:140px;background:var(--white)}
.back-brand-mark{left:80px;top:10px;width:48px;height:48px;border-radius:50%;background:var(--orange)}
.back-brand-name{left:22px;top:66px;width:164px;text-align:center;color:var(--orange);font-weight:700;font-size:21px;line-height:1}
.back-brand-sub{left:22px;top:94px;width:164px;text-align:center;color:var(--orange);font-weight:700;font-size:11px;letter-spacing:2px;line-height:1}
.cert-badge{top:8px;width:30px;height:32px;border:1.5px solid #555;border-radius:3px;background:#f6f6f6}
.trade-name{left:318px;top:12px;font-weight:900;font-size:19px;color:var(--orange)}
.quote-text{left:200px;top:56px;width:268px;white-space:normal;font-style:italic;font-weight:700;font-size:7.4px;line-height:1.35;color:var(--ink)}
.back-contact{left:192px;top:86px;width:288px;height:43px;background:var(--orange)}
</style>
</head>
<body>

<!-- FRONT SIDE -->
<section class="flyer flyer-front" aria-label="Front of flyer">
  <svg class="front-shapes" width="478" height="670" viewBox="0 0 478 670" aria-hidden="true">
    <polygon points="0,187 478,120 478,278 0,395" fill="var(--orange)"/>
    <polygon points="0,395 478,278 478,670 0,670" fill="var(--charcoal)"/>
  </svg>
  <div class="abs camera-photo" role="img" aria-label="Photo of a white bullet CCTV camera with red-lit lens"></div>

  <div class="abs brand-mark" aria-hidden="true"></div>
  <div class="abs brand-name">KELVOR GUARD</div>
  <div class="abs brand-sub" style="display:flex;align-items:center;justify-content:center;gap:6px">
    <span class="brand-rule"></span>INSTALLATIONS<span class="brand-rule"></span>
  </div>

  <h1 class="abs alarm-title">INTRUDER<br>ALARMS</h1>
  <div class="abs alarm-from">STARTING FROM</div>
  <div class="abs alarm-price cond">£495 + VAT</div>

  <svg class="abs discount-badge" viewBox="0 0 155 141" aria-hidden="true">
    <polygon points="38,2 117,2 153,70 117,139 38,139 2,70" fill="var(--white)"/>
    <polygon points="42,9 113,9 145,70 113,132 42,132 10,70" fill="none" stroke="#777" stroke-width="1.2" stroke-dasharray="4 3"/>
  </svg>
  <div class="abs discount-text">
    <div class="discount-amount cond">£150</div>
    <div class="discount-word">DISCOUNT</div>
    <div class="discount-on">ON INSTALLATIONS</div>
    <div class="discount-terms">*terms and conditions<br>apply</div>
  </div>

  <h2 class="abs provider-question cond">Not happy with your<br>current provider?</h2>
  <div class="abs offer-box">
    <div class="abs offer-free cond">FREE OF CHARGE</div>
    <div class="abs offer-small cond">NO OBLIGATION TAKE OVER SURVEY<br>AND QUOTATION AND UP TO</div>
    <div class="abs offer-amount cond">£100</div>
    <div class="abs offer-off cond">OFF</div>
  </div>

  <div class="abs cctv-line">CCTV SYSTEMS STARTING FROM</div>
  <div class="abs cctv-note">(BASED ON 2 CAMERAS)</div>
  <div class="abs cctv-price-disc"><span class="cond">£595</span></div>
  <div class="abs cctv-vat">+ VAT</div>

  <div class="abs call-band">
    <div class="abs call-label">CALL US !</div>
    <svg class="abs call-icon" viewBox="0 0 32 32" aria-hidden="true">
      <circle cx="16" cy="16" r="14.5" fill="none" stroke="var(--ink)" stroke-width="2"/>
      <path d="M11 8.5l3 3-1.8 2.2c1 2 2.6 3.6 4.6 4.6l2.2-1.8 3 3-2 2.3c-5.5-.6-10.6-5.7-11.2-11.2z" fill="var(--ink)"/>
    </svg>
    <div class="abs call-number">01632 908417</div>
  </div>

  <footer class="abs front-footer">
    <div class="abs contact-item" style="left:28px;top:9px">
      <span class="contact-dot"><svg width="9" height="9" viewBox="0 0 10 10" aria-hidden="true"><path d="M5 1L1 5h1.3v4h5.4V5H9z" fill="#fff"/></svg></span>
      <span>14 Marlow Lane,<br>Brentwood, Essex, CM15-9QT</span>
    </div>
    <div class="abs contact-item" style="left:170px;top:15px">
      <span class="contact-dot"><svg width="9" height="9" viewBox="0 0 10 10" aria-hidden="true"><rect x="1" y="2.5" width="8" height="5.5" fill="#fff"/><path d="M1 2.5l4 3 4-3" stroke="var(--orange)" fill="none"/></svg></span>
      <span>operations@kelvorguardinstalls.co.uk</span>
    </div>
    <div class="abs contact-item" style="left:327px;top:15px">
      <span class="contact-dot"><svg width="9" height="9" viewBox="0 0 10 10" aria-hidden="true"><circle cx="5" cy="5" r="4" fill="none" stroke="#fff"/><path d="M1 5h8M5 1v8" stroke="#fff"/></svg></span>
      <span>www.kelvorguardinstalls.co.uk</span>
    </div>
  </footer>
</section>

<!-- BACK SIDE -->
<section class="flyer flyer-back" aria-label="Back of flyer">
  <header class="abs back-header">
    <h2 class="abs header-q1 cond">ARE YOU LOOKING TO</h2>
    <div class="abs header-q2 cond">KEEP YOU AND YOUR PREMISES</div>
    <div class="abs header-safe cond">SAFE?</div>
  </header>

  <div class="abs keypad-photo" role="img" aria-label="Photo of a wall-mounted alarm keypad showing a welcome screen, in a bright modern home"></div>

  <div class="abs back-dark">
    <ul class="abs benefit-list">
      <li><svg class="benefit-tick" viewBox="0 0 11 11" aria-hidden="true"><rect width="11" height="11" fill="var(--orange)"/><path d="M2.5 5.5l2 2 4-4.5" stroke="#fff" stroke-width="1.5" fill="none"/></svg>Kelvor Guard Installations <b>install, maintain and repair</b> all intruder alarms, CCTV, intercom and access control</li>
      <li><svg class="benefit-tick" viewBox="0 0 11 11" aria-hidden="true"><rect width="11" height="11" fill="var(--orange)"/><path d="M2.5 5.5l2 2 4-4.5" stroke="#fff" stroke-width="1.5" fill="none"/></svg>View, control and manage your security systems <b>anywhere in the world</b></li>
      <li><svg class="benefit-tick" viewBox="0 0 11 11" aria-hidden="true"><rect width="11" height="11" fill="var(--orange)"/><path d="M2.5 5.5l2 2 4-4.5" stroke="#fff" stroke-width="1.5" fill="none"/></svg>Feel at ease with monitoring services &amp; police response tailored to suit you and your business</li>
      <li><svg class="benefit-tick" viewBox="0 0 11 11" aria-hidden="true"><rect width="11" height="11" fill="var(--orange)"/><path d="M2.5 5.5l2 2 4-4.5" stroke="#fff" stroke-width="1.5" fill="none"/></svg>Kelvor Guard can takeover any existing security system and offer maintenance checks to guarantee the best performance for you and your premises</li>
      <li><svg class="benefit-tick" viewBox="0 0 11 11" aria-hidden="true"><rect width="11" height="11" fill="var(--orange)"/><path d="M2.5 5.5l2 2 4-4.5" stroke="#fff" stroke-width="1.5" fill="none"/></svg>Kelvor Guard understand that being security conscious is ever increasing, protecting your property and family is a number one priority</li>
      <li><svg class="benefit-tick" viewBox="0 0 11 11" aria-hidden="true"><rect width="11" height="11" fill="var(--orange)"/><path d="M2.5 5.5l2 2 4-4.5" stroke="#fff" stroke-width="1.5" fill="none"/></svg>Our fully insured and accredited team <b>offer quality, safety and cost efficiency</b> throughout the whole process</li>
      <li><svg class="benefit-tick" viewBox="0 0 11 11" aria-hidden="true"><rect width="11" height="11" fill="var(--orange)"/><path d="M2.5 5.5l2 2 4-4.5" stroke="#fff" stroke-width="1.5" fill="none"/></svg>Kelvor Guard Installations are using the latest <b>cloud-based technology</b> to stay connected with your home and business <span class="hl">24/7</span></li>
    </ul>
    <div class="abs app-photo" role="img" aria-label="Photo of two smartphones showing a security control app"></div>
  </div>

  <div class="abs back-white">
    <div class="abs back-brand-mark" aria-hidden="true"></div>
    <div class="abs back-brand-name">KELVOR GUARD</div>
    <div class="abs back-brand-sub" style="display:flex;align-items:center;justify-content:center;gap:6px">
      <span class="brand-rule" style="width:18px"></span>INSTALLATIONS<span class="brand-rule" style="width:18px"></span>
    </div>

    <div class="abs cert-badge" style="left:212px" role="img" aria-label="NQPRB intruder alarm systems certification badge"></div>
    <div class="abs cert-badge" style="left:246px" role="img" aria-label="Accreditation badge"></div>
    <div class="abs cert-badge" style="left:280px;border-radius:50%" role="img" aria-label="NQPRB CCTV systems certification badge"></div>
    <div class="abs trade-name">Tradevouch</div>

    <p class="abs quote-text">If you are looking to improve the security in your home, office or commercial property then call a member of our team today for a free quote.</p>

    <footer class="abs back-contact">
      <div class="abs contact-item" style="left:6px;top:3px;font-size:7px">
        <span class="contact-dot" style="width:13px;height:13px;background:var(--white)"><svg width="7" height="7" viewBox="0 0 10 10" aria-hidden="true"><path d="M5 1L1 5h1.3v4h5.4V5H9z" fill="var(--orange)"/></svg></span>
        <span>14 Marlow Lane,<br>Brentwood, Essex, CM15-9QT</span>
      </div>
      <div class="abs contact-item" style="left:6px;top:26px;font-size:8px">
        <span class="contact-dot" style="width:13px;height:13px;background:var(--white)"><svg width="7" height="7" viewBox="0 0 10 10" aria-hidden="true"><path d="M2 1l2 2-1 1.5c.6 1.2 1.4 2 2.6 2.6L7 6l2 2-1.3 1.5C4.5 9 1 5.5.5 2.3z" fill="var(--orange)"/></svg></span>
        <span>01632 908417</span>
      </div>
      <div class="abs contact-item" style="left:132px;top:7px;font-size:7px">
        <span class="contact-dot" style="width:13px;height:13px;background:var(--white)"><svg width="7" height="7" viewBox="0 0 10 10" aria-hidden="true"><rect x="1" y="2.5" width="8" height="5.5" fill="var(--orange)"/></svg></span>
        <span>operations@kelvorguardinstalls.co.uk</span>
      </div>
      <div class="abs contact-item" style="left:132px;top:24px;font-size:7px">
        <span class="contact-dot" style="width:13px;height:13px;background:var(--white)"><svg width="7" height="7" viewBox="0 0 10 10" aria-hidden="true"><circle cx="5" cy="5" r="4" fill="none" stroke="var(--orange)"/><path d="M1 5h8M5 1v8" stroke="var(--orange)"/></svg></span>
        <span>www.kelvorguardinstalls.co.uk</span>
      </div>
    </footer>
  </div>
</section>

</body>
</html>
```